Process Serving Company needs a letterhead design

Looking to have a letterhead designed for letters to attorneys advertising our business. We would like something eye catching but professional. Colors and logos are attached. Please add "Process Service and Attorney Support" near the logo or header

Target Market(s)

Attorneys

Font styles to use
Serif
Sans Serif

Colors
33a6d7
0255a3
85cae6
cee9f5
ecf7fb

```html
<!DOCTYPE html>
<html lang="en">
<head>
<meta charset="utf-8">
<title>Canyon Ridge Serve Letterhead</title>
<link href="https://fonts.googleapis.com/css2?family=Arimo:wght@700&family=Source+Sans+3:wght@400;600;700&display=swap" rel="stylesheet">
<style>
:root{
  --brand-blue:#33a6d7;
  --brand-navy:#0255a3;
  --brand-light:#85cae6;
  --brand-pale:#cee9f5;
  --paper:#f8f8f8;
  --backdrop:#e4e4e4;
  --ink:#4a4a4a;
  --ink-dark:#333333;
}
html,body{margin:0;padding:0;width:1059px;height:1200px;overflow:hidden;background:var(--backdrop);}
.letterhead{
  position:absolute;left:113px;top:12px;width:832px;height:1175px;
  background:var(--paper);box-shadow:0 4px 18px rgba(0,0,0,.18);
  font-family:"Source Sans 3",sans-serif;color:var(--ink);
}
.brand{position:absolute;left:69px;top:56px;display:flex;align-items:center;gap:12px;}
.brand-mark{width:22px;height:22px;background:var(--brand-blue);}
.brand-name{font-size:34px;font-weight:400;color:var(--brand-blue);letter-spacing:.5px;line-height:1;}
.salutation{
  position:absolute;left:71px;top:268px;margin:0;
  font-family:"Arimo",sans-serif;font-weight:700;font-size:18px;color:var(--ink);
}
.letter-body{position:absolute;left:71px;top:318px;width:697px;}
.letter-body p{margin:0 0 21.8px;font-size:16.6px;line-height:21.8px;text-align:justify;}
.signature{position:absolute;left:71px;top:829px;width:155px;height:74px;background:#ececec;border-radius:4px;}
.footer-bar{position:absolute;left:61px;top:1103px;width:14px;height:72px;background:var(--brand-blue);}
.footer-info{position:absolute;left:82px;top:1099px;font-size:11px;line-height:17.5px;color:var(--ink-dark);}
.footer-info .company{font-weight:700;color:var(--brand-blue);}
.footer-info .label{font-weight:700;color:var(--brand-blue);}
.footer-info .sep{margin:0 4px;}
.footer-rule{position:absolute;left:75px;top:1155px;width:545px;height:1px;background:var(--brand-navy);}
.web-tag{position:absolute;left:614px;top:1145px;}
</style>
</head>
<body>
<main class="letterhead">
  <header class="brand">
    <span class="brand-mark"></span>
    <span class="brand-name">Canyon Ridge Serve</span>
  </header>

  <h1 class="salutation">Dear Mr. Hale,</h1>

  <section class="letter-body">
    <p>Lorem Ipsum is simply dummy text of the printing and typesetting industry. Lorem Ipsum has been the industry's standard dummy text ever since the 1500s, when an unknown printer took a galley of type and scrambled it to make a type specimen book. It has survived not only five centuries, but also the leap into electronic typesetting, remaining essentially unchanged.</p>
    <p>The standard chunk of Lorem Ipsum used since the 1500s is reproduced below for those interested. Sections 1.10.32 and 1.10.33 from "de Finibus Bonorum et Malorum" by Cicero are also reproduced in their exact original form, accompanied by English versions from the 1914 translation by H. Rackham</p>
    <p>Lorem Ipsum is simply dummy text of the printing and typesetting industry. Lorem Ipsum has been the industry's standard dummy text ever since the 1500s, when an unknown printer took a galley of type and scrambled it to make a type specimen book. It has survived not only five centuries, but also the leap into electronic typesetting, remaining essentially unchanged. It was popularised in the</p>
    <p>The standard chunk of Lorem Ipsum used since the 1500s is reproduced below for those interested. Sections 1.10.32 and 1.10.33 from "de Finibus Bonorum et Malorum" by Cicero are also reproduced in their exact original form, accompanied by English versions from the 1914 translation by H. Rackham</p>
  </section>

  <div class="signature" role="img" aria-label="Handwritten signature of the sender"></div>

  <footer>
    <div class="footer-bar"></div>
    <div class="footer-info">
      <div class="company">Canyon Ridge Serve</div>
      <div>4120 E Mesa Vista Rd #210 Tempe AZ 85281</div>
      <div><span class="label">Phone:</span> 555-201-4470<span class="sep">|</span><span class="label">Fax:</span> 555-201-4471<span class="sep">|</span><span class="label">Mail:</span> info@canyonridgeserve.com</div>
    </div>
    <div class="footer-rule"></div>
    <svg class="web-tag" width="170" height="21" viewBox="0 0 170 21">
      <polygon points="8,0 162,0 170,10.5 162,21 8,21 0,10.5" fill="var(--brand-blue)"/>
      <text x="85" y="15" text-anchor="middle" font-family="Source Sans 3, sans-serif" font-size="13" fill="#ffffff" letter-spacing=".6">www.canyonridgeserve.com</text>
    </svg>
  </footer>
</main>
</body>
</html>
```